Tide & Thistle Website Creation For Online Spirits Sales via MerrowVats.com

Want a Website developed that I will use to partner with Merrow Vats to sell my signature rum online. Merrow Vats will add the final code to make the website an e-commerce site. Website should have links to Social media pages, recipies, About, news and events, products. I have he domain name already just need a designer to make the website look professional. Need website capable of being viewed on iPhone and Android devices. Please use the color scheme that is on the label. The brand motto is: Celebrate Life With Family old and new friends. The bottle sent in the images will be replaced with and actual high resolution image of the bottle when it is produce on 27 DEC 21. Can give the selected designer access to develop the website. I have the hostbramble.com domain name. Final code will be added by a designer from MerrowVats.com to make it a e-commerce store.
Updates

I added more information to refine the design I wanted. I should have had this information available to the designers when I started the project.

Target Market(s)

Target Market is 25-50 year old who drink rum

Industry/Entity Type

Spirits. Using Website to sell Rum online

Number of Pages Required

1 page

Font styles to use
Sans Serif

Colors
00AB8E
00BBA5
67D7C9
C6EFE9
E9F9F6

Requirements
Must have
• Must look elegant and of high class. Rum is being market as a premium unnamed rum.
Nice to have
• Video of people drinking, smiling and celebrating

```html
<!DOCTYPE html>
<html lang="en">
<head>
<meta charset="utf-8">
<title>Tide &amp; Thistle</title>
<link href="https://fonts.googleapis.com/css2?family=Poppins:ital,wght@0,400;0,500;0,600;0,700;1,400&display=swap" rel="stylesheet">
<style>
:root{
  --green:#1a9e7e;
  --green-dark:#12876b;
  --teal-soft:#c6efe9;
  --teal-pale:#e9f9f6;
  --ink:#1c1c1c;
  --text:#555;
  --dark:#1e2021;
  --sol-bg:#f3fafc;
}
*{box-sizing:border-box;margin:0;padding:0}
html,body{width:1200px;height:3565px;overflow:hidden}
body{font-family:'Poppins',sans-serif;color:var(--ink);position:relative;background:#fff}
.abs{position:absolute}
.btn{position:absolute;display:flex;align-items:center;justify-content:center;color:#fff;font-size:15px;font-weight:500;background:var(--green)}
.h2{font-size:41px;font-weight:700;color:var(--green)}
.rule{height:4px;width:92px;background:var(--green)}
.p{font-size:12.5px;line-height:29px;color:var(--text)}

/* header */
.topbar{left:415px;top:0;width:785px;height:56px;background:var(--teal-pale)}
.topbar .item{position:absolute;top:10px;display:flex;align-items:center;gap:8px;font-size:13.5px;color:#444}
.topbar .dot{width:38px;height:38px;border-radius:50%;background:var(--green);border:3px solid #9edfd3;display:flex;align-items:center;justify-content:center}
.logo{left:110px;top:14px;width:190px;text-align:center}
.logo .mark{width:58px;height:58px;border-radius:50%;background:var(--ink);margin:0 auto 6px}
.logo .name{font-size:25px;font-weight:600;letter-spacing:.5px}
.nav{top:83px;left:384px;display:flex;gap:22px;font-size:13px;font-weight:500}
/* hero */
.hero-photo{left:0;top:126px;width:760px;height:691px;background:linear-gradient(120deg,#2a2826,#0f1012 60%,#1c2433)}
.hero-side{left:755px;top:126px;width:445px;height:691px;background:var(--green)}
.hero-curve{left:560px;top:126px;width:220px;height:691px}
.hero-bottle{left:605px;top:265px;width:185px;height:552px;background:linear-gradient(180deg,#e8e3d6 0%,#c98a34 35%,#b87420 70%,#8d5817 100%);border-radius:60px 60px 20px 20px}
.hero-title{left:770px;top:280px;width:400px;text-align:center;font-size:50px;font-weight:700;color:#fff}
.hero-text{left:805px;top:360px;width:330px;text-align:center;font-size:13px;line-height:29px;color:#e9f9f6}
/* solutions */
.solutions{left:0;top:1508px;width:1200px;height:497px;background:var(--sol-bg)}
.sol{position:absolute;top:1705px;width:220px;text-align:center}
.sol .ring{width:108px;height:108px;margin:0 auto;border-radius:50%;border:5px dashed var(--green);display:flex;align-items:center;justify-content:center}
.sol h3{font-size:15px;font-weight:600;margin-top:26px}
.sol p{font-size:11.5px;line-height:21px;color:var(--text);margin-top:8px}
/* testimonials */
.testi{left:0;top:2610px;width:1200px;height:495px;background:linear-gradient(180deg,#1a1b1c,#2a2725)}
.card{position:absolute;top:2835px;width:315px;height:212px;background:#fff;border-radius:6px;padding:22px 20px}
.card .q{font-size:30px;font-weight:700;color:var(--green);line-height:26px}
.card p{font-size:12px;font-style:italic;line-height:24px;color:#555;margin-top:8px}
.card .who{display:flex;align-items:center;gap:10px;margin-top:14px;font-size:13px}
.card .av{width:52px;height:52px;border-radius:50%;background:linear-gradient(#d8c2b3,#a9816c)}
.arrow{position:absolute;top:2924px;width:34px;height:34px;border-radius:50%;background:#fff;display:flex;align-items:center;justify-content:center}
/* footer */
.fh{position:absolute;top:3202px;font-size:14px;font-weight:500;color:#333}
.fl{position:absolute;font-size:13.5px;color:#333;line-height:34px}
.soc{display:flex;align-items:center;gap:8px;height:40px;font-size:13.5px;color:#333}
.soc i{width:32px;height:32px;border:2px solid #222;border-radius:50%;display:block}
</style>
</head>
<body>

<header>
  <div class="abs topbar">
    <div class="item" style="left:33px"><span class="dot"><svg width="14" height="14" viewBox="0 0 24 24" fill="#fff"><path d="M6.6 10.8a15 15 0 0 0 6.6 6.6l2.2-2.2a1 1 0 0 1 1-.3 11 11 0 0 0 3.6.6 1 1 0 0 1 1 1V20a1 1 0 0 1-1 1A17 17 0 0 1 3 4a1 1 0 0 1 1-1h3.5a1 1 0 0 1 1 1c0 1.3.2 2.5.6 3.6a1 1 0 0 1-.3 1z"/></svg></span>Call Now - 123-456-7890</div>
    <div class="item" style="left:280px"><span class="dot"><svg width="14" height="12" viewBox="0 0 24 18" fill="#fff"><path d="M0 0h24v18H0z" opacity=".9"/><path d="M0 0l12 9 12-9" stroke="#1a9e7e" stroke-width="2" fill="none"/></svg></span>Email Now - info@Tide&amp;Thistle.com</div>
    <div class="item" style="left:605px;top:24px;gap:12px"><i style="width:8px;height:8px;background:#222;display:block"></i><i style="width:8px;height:8px;background:#222;display:block"></i><i style="width:8px;height:8px;background:#222;display:block"></i></div>
  </div>
  <div class="abs logo"><div class="mark"></div><div class="name">TIDE &amp; THISTLE</div></div>
  <nav class="abs nav"><span>DTC Solutions</span><span>Pourhaven</span><span>International</span><span>Why Tide &amp; Thistle</span></nav>
  <div class="btn" style="left:845px;top:70px;width:117px;height:45px;font-size:14px">Contact</div>
  <div class="btn" style="left:972px;top:70px;width:116px;height:45px;font-size:14px;background:#27b89c">Signup</div>
</header>

<section class="hero">
  <div class="abs hero-photo" role="img" aria-label="Photo of a man in a suit holding a glass of rum"></div>
  <svg class="abs hero-curve" viewBox="0 0 220 691" preserveAspectRatio="none"><path d="M170 0H220V691H0C120 640 175 560 170 420Z" fill="#b7ebe1"/><path d="M195 0H220V691H40C150 640 200 560 195 420Z" fill="#1a9e7e"/></svg>
  <div class="abs hero-side"></div>
  <div class="abs hero-bottle" role="img" aria-label="Bottle of Tide and Thistle rum"></div>
  <h1 class="abs hero-title">Tide &amp; Thistle</h1>
  <p class="abs hero-text">Lorem ipsum dolor sit amet, consectetur adipiscing elit, sed do eiusmod tempor incididunt ut labore et dolore magna aliqua. Ut enim ad minim veniam, quis nostrud exercitation ullamco laboris nisi ut aliquip ex ea commodo consequat. Duis aute irure dolor in reprehenderit in voluptate velit esse cillum dolore</p>
  <div class="btn" style="left:857px;top:588px;width:226px;height:60px;background:#111">Get Started</div>
</section>

<section class="about">
  <h2 class="abs h2" style="left:111px;top:940px">About Us</h2>
  <div class="abs rule" style="left:111px;top:1005px"></div>
  <p class="abs p" style="left:111px;top:1038px;width:450px">Lorem ipsum dolor sit amet, consectetur adipiscing elit, tempor incididunt ut labore et dolore magna aliqua. Ut enim ad minim veniam, exercitation ullamco laboris nisi ut aliquip ex ea commodo consequat. Duis aute irure dolor in reprehenderit in voluptate velit esse cillum dolore eu fugiat nulla pariatur. Excepteur sint occaecat cupidatat non proident, sunt in culpa qui officia deserunt mollit anim id est laborum.</p>
  <p class="abs p" style="left:111px;top:1230px;width:450px">Lorem ipsum dolor sit amet, consectetur adipiscing elit, incididunt ut labore et dolore magna aliqua. Ut enim ad minim veniam,</p>
  <div class="btn" style="left:111px;top:1313px;width:227px;height:60px">Read More</div>
  <svg class="abs" style="left:604px;top:918px" width="482" height="482" viewBox="0 0 482 482"><circle cx="241" cy="241" r="236" fill="none" stroke="#1a9e7e" stroke-width="9" stroke-dasharray="120 6"/></svg>
  <div class="abs" style="left:621px;top:935px;width:448px;height:448px;border-radius:50%;background:radial-gradient(circle at 50% 70%,#9a5a1e,#2a2422 45%,#121314)" role="img" aria-label="Crystal decanter and two glasses of rum"></div>
</section>

<div class="abs" style="left:1030px;top:1453px;width:135px;height:137px;background:linear-gradient(180deg,#e9ecec 30%,#b8561a 60%,#6e2a0c);border-radius:6px" role="img" aria-label="Glass of rum on the rocks"></div>

<section>
  <div class="abs solutions"></div>
  <svg class="abs" style="left:375px;top:1535px" width="450" height="450" viewBox="0 0 450 450"><circle cx="225" cy="225" r="205" fill="none" stroke="#e6edef" stroke-width="34"/></svg>
  <h2 class="abs h2" style="left:0;top:1580px;width:1200px;text-align:center">Our Solutions</h2>
  <div class="abs rule" style="left:554px;top:1645px"></div>
  <div class="sol" style="left:107px"><div class="ring"><svg width="46" height="46" viewBox="0 0 24 24" fill="none" stroke="#1a9e7e" stroke-width="1.5"><path d="M3 12V4h8l10 10-8 8z"/><circle cx="7.5" cy="7.5" r="1.5"/></svg></div><h3>White-Label</h3><p>Lorem ipsum dolor consectetur adipiscing elit, sed do eiusmod tempor incididunt ut labor</p></div>
  <div class="sol" style="left:362px"><div class="ring"><svg width="46" height="46" viewBox="0 0 24 24" fill="none" stroke="#1a9e7e" stroke-width="1.5"><path d="M20 12a8 8 0 0 1-14 5M4 12a8 8 0 0 1 14-5"/><path d="M18 3v4h-4M6 21v-4h4"/><circle cx="12" cy="12" r="3"/></svg></div><h3>Subscriptions</h3><p>Lorem ipsum dolor consectetur adipiscing elit, sed do eiusmod tempor incididunt ut labor</p></div>
  <div class="sol" style="left:618px"><div class="ring"><svg width="46" height="46" viewBox="0 0 24 24" fill="none" stroke="#1a9e7e" stroke-width="1.5"><path d="M4 20V15M8 20v-7M12 20v-5M16 20v-9M20 20V8M3 21h18"/><path d="M4 12l4-3 4 2 4-4 4-3"/></svg></div><h3>Analytics Suite</h3><p>Lorem ipsum dolor consectetur adipiscing elit, sed do eiusmod tempor incididunt ut labor</p></div>
  <div class="sol" style="left:873px"><div class="ring"><svg width="46" height="46" viewBox="0 0 24 24" fill="none" stroke="#1a9e7e" stroke-width="1.5"><rect x="9" y="9" width="6" height="6"/><rect x="2" y="2" width="5" height="5"/><rect x="17" y="2" width="5" height="5"/><rect x="2" y="17" width="5" height="5"/><rect x="17" y="17" width="5" height="5"/><path d="M7 7l2 2M17 7l-2 2M7 17l2-2M17 17l-2-2"/></svg></div><h3>Direct Marketing</h3><p>Lorem ipsum dolor consectetur adipiscing elit, sed do eiusmod tempor incididunt ut labor</p></div>
</section>

<section class="product">
  <div class="abs" style="left:111px;top:2132px;width:300px;height:323px;background:#27b69b"></div>
  <div class="abs" style="left:206px;top:2200px;width:318px;height:322px;border:2px dashed var(--green)"></div>
  <div class="abs" style="left:240px;top:2170px;width:100px;height:330px;background:linear-gradient(180deg,#e8e3d6,#c98a34 35%,#8d5817);border-radius:40px 40px 14px 14px" role="img" aria-label="Small bottle of Tide and Thistle rum"></div>
  <div class="abs" style="left:360px;top:2100px;width:145px;height:425px;background:linear-gradient(180deg,#e8e3d6,#c98a34 30%,#8d5817);border-radius:55px 55px 18px 18px" role="img" aria-label="Large bottle of Tide and Thistle rum"></div>
  <h2 class="abs h2" style="left:600px;top:2130px">Our Product</h2>
  <div class="abs rule" style="left:600px;top:2195px"></div>
  <p class="abs p" style="left:600px;top:2222px;width:500px">Lorem ipsum dolor sit amet, consectetur adipiscing elit, sed tempor incididunt ut labore et dolore magna aliqua. Ut enim ad minim veniam, quis exercitation ullamco laboris nisi ut aliquip ex ea commodo consequat. Duis aute irure dolor in reprehenderit in voluptate velit esse cillum dolore eu fugiat nulla pariatur. Excepteur sint occaecat cupidatat non proident, sunt in culpa qui officia deserunt mollit anim id est laborum</p>
  <div class="btn" style="left:600px;top:2424px;width:226px;height:59px">Buy Now</div>
</section>

<section>
  <div class="abs testi" role="img" aria-label="Dark photo of bottles and glasses"></div>
  <h2 class="abs h2" style="left:0;top:2658px;width:1200px;text-align:center;color:#fff">Client Testimonials</h2>
  <div class="abs rule" style="left:554px;top:2723px;background:#fff"></div>
  <p class="abs p" style="left:290px;top:2750px;width:620px;text-align:center;color:#fff;font-size:13.5px">Lorem ipsum dolor sit amet, consectetur adipiscing elit, sed do eiusmod tempor incididunt ut labore et dolore magna aliqua. Ut enim ad minim veniam,</p>
  <div class="arrow" style="left:64px"><svg width="16" height="16" viewBox="0 0 24 24" fill="none" stroke="#111" stroke-width="3"><path d="M20 12H5M11 5l-7 7 7 7"/></svg></div>
  <div class="arrow" style="left:1099px"><svg width="16" height="16" viewBox="0 0 24 24" fill="none" stroke="#111" stroke-width="3"><path d="M4 12h15M13 5l7 7-7 7"/></svg></div>
  <div class="card" style="left:111px"><div class="q">&ldquo;</div><p>Lorem ipsum dolor sit amet, consectetur adipiscing elit, sed do eiusmod tempor incididunt ut labore et dolore magna aliqua.</p><div class="who"><span class="av" role="img" aria-label="Client portrait"></span>Nell Arbery</div></div>
  <div class="card" style="left:441px"><div class="q">&ldquo;</div><p>Lorem ipsum dolor sit amet, consectetur adipiscing elit, sed do eiusmod tempor incididunt ut labore et dolore magna aliqua.</p><div class="who"><span class="av" role="img" aria-label="Client portrait"></span>Nell Arbery</div></div>
  <div class="card" style="left:771px"><div class="q">&ldquo;</div><p>Lorem ipsum dolor sit amet, consectetur adipiscing elit, sed do eiusmod tempor incididunt ut labore et dolore magna aliqua.</p><div class="who"><span class="av" role="img" aria-label="Client portrait"></span>Nell Arbery</div></div>
</section>

<footer>
  <div class="fh" style="left:127px">QUICKLINKS</div>
  <div class="fl" style="left:129px;top:3238px">DTC Solutions<br>Pourhaven<br>International<br>Why Tide &amp; Thistle.</div>
  <div class="fh" style="left:310px">CONTACT US</div>
  <div class="fl" style="left:312px;top:3244px;line-height:28px">
    <div style="display:flex;gap:20px"><svg width="16" height="16" viewBox="0 0 24 24" fill="none" stroke="#333" stroke-width="1.6" style="margin-top:6px"><path d="M6.6 10.8a15 15 0 0 0 6.6 6.6l2.2-2.2 4.6 1V20A17 17 0 0 1 3 4h4.5l1 4.6z"/></svg>123-456-7890</div>
    <div style="display:flex;gap:16px;margin-top:14px"><svg width="16" height="18" viewBox="0 0 24 24" fill="#333" style="margin-top:6px"><path d="M12 2a7 7 0 0 0-7 7c0 5 7 13 7 13s7-8 7-13a7 7 0 0 0-7-7zm0 9.5A2.5 2.5 0 1 1 12 6.5a2.5 2.5 0 0 1 0 5z"/></svg><span>Lorem ipsum dolor sit amet,<br>consectetur adipiscing</span></div>
    <div style="display:flex;gap:16px;margin-top:14px"><svg width="16" height="12" viewBox="0 0 24 18" fill="none" stroke="#333" stroke-width="1.6" style="margin-top:8px"><rect x="1" y="1" width="22" height="16"/><path d="M1 1l11 9 11-9"/></svg>info@Tide&amp;Thistle.com</div>
  </div>
  <div class="fh" style="left:603px">CONNECT WITH US</div>
  <div class="fl" style="left:598px;top:3244px">
    <div class="soc"><i></i>Friendwall</div><div class="soc"><i></i>Snapgrid</div><div class="soc"><i></i>Chirpline</div><div class="soc"><i></i>Workmesh</div>
  </div>
  <div class="fh" style="left:840px">NEWSLETTER</div>
  <div class="abs" style="left:840px;top:3255px;width:248px;height:45px;border:1px solid #bbb;font-size:13px;color:#777;padding:13px 10px">Enter Name</div>
  <div class="btn" style="left:840px;top:3315px;width:136px;height:43px;font-size:15px;font-weight:600">SUBSCRIBE</div>
  <div class="abs" style="left:838px;top:3380px;font-size:22px;font-weight:700;color:#1f3d7a">Paybrook</div>
  <div class="abs" style="left:838px;top:3412px;font-size:12px;font-weight:700;color:#1f3d7a">Cardiva</div>
  <div class="abs" style="left:127px;top:3470px;width:960px;height:1px;background:#ddd"></div>
  <div class="abs" style="left:0;top:3505px;width:1200px;text-align:center;font-size:14px;color:#333">copyrights &copy; 2021 All Rights Reserved</div>
  <div class="abs" style="left:50px;top:3425px;width:137px;height:138px;background:linear-gradient(180deg,#eef0f0 25%,#c65a18 55%,#6e2a0c);border-radius:6px" role="img" aria-label="Glass of rum on the rocks"></div>
</footer>

</body>
</html>
```